Copper Ridge Inquiries Letterhead

I would like to design a letterhead for a private investigation company. Our primary clients will be law firms. The business card is included below

```html
<!DOCTYPE html>
<html lang="en">
<head>
<meta charset="utf-8">
<title>Copper Ridge Inquiries Letterhead</title>
<link rel="stylesheet" href="https://fonts.googleapis.com/css2?family=Work+Sans:wght@400;500;700&display=swap">
<style>
  :root {
    --navy: #173462;
    --orange: #f15f32;
    --paper: #f7f7f6;
    --backdrop: #dcdcdc;
    --white: #ffffff;
  }
  * { margin: 0; padding: 0; box-sizing: border-box; }
  html, body {
    width: 1200px; height: 686px; overflow: hidden;
    background: var(--backdrop);
    font-family: "Work Sans", Arial, sans-serif;
  }
  .letterhead {
    position: absolute; left: 365px; top: 39px;
    width: 470px; height: 608px;
    background: var(--paper);
    box-shadow: 0 6px 18px rgba(0,0,0,.18);
    overflow: hidden;
  }
  .letterhead__art { position: absolute; inset: 0; width: 100%; height: 100%; }
  .brand {
    position: absolute; left: 30px; top: 72px;
    display: flex; align-items: center; gap: 8px;
    white-space: nowrap;
  }
  .brand__dot {
    width: 14px; height: 14px; border-radius: 50%;
    background: var(--orange); flex: none;
  }
  .brand__name {
    font-size: 14px; font-weight: 700; color: var(--navy);
    letter-spacing: .02em;
  }
  .contact {
    position: absolute; right: 14px; top: 22px;
    list-style: none; text-align: right;
    color: var(--white); font-size: 10.5px; line-height: 16px;
    white-space: nowrap;
  }
  .contact__item { display: flex; justify-content: flex-end; align-items: center; gap: 6px; }
  .contact__icon { width: 10px; height: 10px; fill: var(--orange); flex: none; }
  .tagline {
    position: absolute; left: 26px; bottom: 14px;
    color: var(--white); font-size: 10.5px; font-weight: 500;
    letter-spacing: .04em; text-transform: uppercase;
    white-space: nowrap;
  }
</style>
</head>
<body>
  <main class="letterhead">
    <svg class="letterhead__art" viewBox="0 0 470 608" aria-hidden="true">
      <path d="M90,0 C190,8 230,62 285,98 C340,132 400,128 470,132 L470,0 Z" fill="var(--navy)"/>
      <path d="M80,0 C182,10 224,66 280,102 C338,138 400,138 470,140 L470,146 C398,146 332,146 274,108 C218,70 176,14 70,4 Z" fill="var(--orange)"/>
      <path d="M255,104 C300,142 350,152 470,150 L470,154 C350,162 296,150 255,104 Z" fill="var(--navy)"/>
      <path d="M0,546 C70,584 200,566 300,578 C380,588 440,598 470,608 L0,608 Z" fill="var(--orange)"/>
      <path d="M0,532 C70,576 200,556 300,570 C390,582 445,596 470,606 C440,594 380,584 300,574 C200,562 70,580 0,540 Z" fill="var(--navy)"/>
    </svg>

    <div class="brand">
      <span class="brand__dot"></span>
      <span class="brand__name">Copper Ridge Inquiries</span>
    </div>

    <ul class="contact">
      <li class="contact__item">555.014.2290
        <svg class="contact__icon" viewBox="0 0 10 10"><path d="M2,0.5 L3.8,2.6 L2.9,3.6 C3.5,5 4.8,6.4 6.3,7 L7.3,6 L9.5,7.8 L8.3,9.5 C4.5,9.2 0.8,5.5 0.5,1.7 Z"/></svg>
      </li>
      <li class="contact__item">Millbrook, TX
        <svg class="contact__icon" viewBox="0 0 10 10"><path d="M5,0 C7.2,0 8.6,1.6 8.6,3.5 C8.6,6 5,10 5,10 C5,10 1.4,6 1.4,3.5 C1.4,1.6 2.8,0 5,0 Z M5,2.2 A1.3,1.3 0 1 0 5,4.8 A1.3,1.3 0 1 0 5,2.2 Z"/></svg>
      </li>
      <li class="contact__item">License NO. 04729316
        <svg class="contact__icon" viewBox="0 0 10 10"><path d="M0,1.5 H10 V8.5 H0 Z M1.2,3 V7 H4.2 V3 Z M5.2,3.2 H8.8 V4 H5.2 Z M5.2,5 H8.8 V5.8 H5.2 Z"/></svg>
      </li>
      <li class="contact__item">daniel@copperridgeinquiries.com
        <svg class="contact__icon" viewBox="0 0 10 10"><path d="M0,2 H10 V8 H0 Z M0.8,2.6 L5,5.6 L9.2,2.6 L9.2,3.4 L5,6.4 L0.8,3.4 Z" fill-rule="evenodd"/></svg>
      </li>
    </ul>

    <p class="tagline">Over 20 years of investigative experience</p>
  </main>
</body>
</html>
```